Awesome photographers card for an awesome new business

Double sided business card Black background and silver logo in middle on one side. Details on otherside. please keep it simple

Industry/Entity Type

Photographer

Contact Information for Business Card

Gerald Fenwick
0452817360
GeraldFenwickPhotography47@mailbox.test
www.GeraldFenwickPhotography.test.au
Instagram _Gerald_fenwick

Requirements
Must have
• My logo in Silver
• please use instagram logo instead of "Instagram"

```html
<!DOCTYPE html>
<html lang="en">
<head>
<meta charset="utf-8">
<title>Gerald Fenwick Photography – Business Card</title>
<link href="https://fonts.googleapis.com/css2?family=Roboto:wght@400;500&family=Roboto+Condensed:wght@700&display=swap" rel="stylesheet">
<style>
  :root {
    --backdrop: #1d1d1d;
    --card-white: #f4f4f4;
    --band-dark: #5c5c5c;
    --band-light: #b4b4b4;
    --silver-edge: #7a7a7a;
    --silver-mid: #b0b0b0;
    --ink: #454545;
    --white: #ffffff;
    --mark-grey: #8a8a8a;
  }
  * { margin: 0; padding: 0; box-sizing: border-box; }
  html, body { width: 1200px; height: 960px; overflow: hidden; }
  body {
    position: relative;
    background: var(--backdrop);
    font-family: "Roboto", Arial, sans-serif;
  }
  .card {
    position: absolute;
    width: 600px;
    height: 343px;
  }
  .card--front {
    left: 314px; top: 113px;
    background: var(--card-white);
  }
  .card--back {
    left: 311px; top: 472px;
    background: linear-gradient(90deg, var(--silver-edge) 0%, var(--silver-mid) 45%, var(--silver-mid) 60%, var(--silver-edge) 100%);
  }
  .name-band {
    position: absolute;
    left: 0; top: 47px;
    width: 480px; height: 111px;
    background: linear-gradient(90deg, var(--band-dark) 0%, #8c8c8c 50%, var(--band-light) 75%, #7a7a7a 100%);
  }
  .holder-name {
    position: absolute;
    left: 44px; top: 90px;
    font-family: "Roboto Condensed", "Arial Narrow", sans-serif;
    font-weight: 700;
    font-size: 20px;
    color: var(--white);
    letter-spacing: 0.2px;
  }
  .brand-mark {
    position: absolute;
    display: flex;
    align-items: center;
    justify-content: center;
    text-align: center;
    border-radius: 50%;
    font-family: "Roboto", Arial, sans-serif;
    font-weight: 500;
  }
  .brand-mark--front {
    left: 437px; top: 45px;
    width: 114px; height: 114px;
    background: var(--card-white);
    border: 3px solid var(--mark-grey);
    color: var(--mark-grey);
    font-size: 14px;
    line-height: 1.2;
  }
  .brand-mark--back {
    left: 210px; top: 78px;
    width: 180px; height: 180px;
    border: 4px solid #efefef;
    color: #efefef;
    font-size: 20px;
    line-height: 1.2;
  }
  .contact-list {
    position: absolute;
    left: 44px; top: 228px;
    list-style: none;
  }
  .contact-list li {
    display: flex;
    align-items: center;
    height: 19px;
    font-size: 14.5px;
    color: var(--ink);
  }
  .contact-list svg {
    width: 13px; height: 13px;
    margin-right: 12px;
    fill: var(--ink);
    flex: none;
  }
  .back-url {
    position: absolute;
    left: 0; right: 0; top: 291px;
    text-align: center;
    font-size: 15px;
    letter-spacing: 2.3px;
    color: var(--white);
  }
</style>
</head>
<body>

<section class="card card--front" aria-label="Card front">
  <div class="name-band"></div>
  <h1 class="holder-name">GERALD FENWICK</h1>
  <div class="brand-mark brand-mark--front">Gerald<br>Fenwick</div>

  <ul class="contact-list">
    <li>
      <svg viewBox="0 0 16 16" aria-hidden="true"><path d="M3.5 1 6 3.8 4.8 5.6c.8 1.9 3.3 4.6 5.6 5.6L12.2 10 15 12.5 13.4 15C7 15 1 9 1 2.6Z"/></svg>
      0452817360
    </li>
    <li>
      <svg viewBox="0 0 16 16" aria-hidden="true"><path d="M1 3h14v10H1Zm1.5 1.3v.4L8 8.6l5.5-3.9v-.4Z"/></svg>
      GeraldFenwickPhotography47@mailbox.test
    </li>
    <li>
      <svg viewBox="0 0 16 16" aria-hidden="true"><path d="M8 1a7 7 0 1 0 0 14A7 7 0 0 0 8 1Zm0 1.5c1 1 1.7 2.6 1.9 4.5H6.1C6.3 5.1 7 3.5 8 2.5ZM6.1 9h3.8C9.7 10.9 9 12.5 8 13.5 7 12.5 6.3 10.9 6.1 9ZM2.6 7a5.5 5.5 0 0 1 2.8-4 9 9 0 0 0-.8 4Zm0 2h2a9 9 0 0 0 .8 4 5.5 5.5 0 0 1-2.8-4Zm8.8 0h2a5.5 5.5 0 0 1-2.8 4 9 9 0 0 0 .8-4Zm0-2a9 9 0 0 0-.8-4 5.5 5.5 0 0 1 2.8 4Z"/></svg>
      www.GeraldFenwickPhotography.test.au
    </li>
    <li>
      <svg viewBox="0 0 16 16" aria-hidden="true"><rect x="1.5" y="1.5" width="13" height="13" rx="1"/></svg>
      Gerald_fenwick
    </li>
  </ul>
</section>

<section class="card card--back" aria-label="Card back">
  <div class="brand-mark brand-mark--back">Gerald<br>Fenwick</div>
  <p class="back-url">www.GeraldFenwickPhotography.test.au</p>
</section>

</body>
</html>
```